Logo and Website Design for QR.KA Horizon - a Software Engineering and IT company

Software engineering and IT are two different disciplines - and yet inseparably linked. At QR.KA Horizon, we combine both worlds and ensure that our software solutions are not only innovative and powerful, but also integrate perfectly into existing IT landscapes. Vision stands more for imagination, so it is not neccessary something what has to do with visualisation. Please consider that the winning competitor is also instructed to make a logo for the company. So please make a suitable logo for QR.KA Horizon to which the website fits to and show it during the website creation process. A good Logo desing is important for winning the competition. The website should contain a landing page with inspiring, perhaps futuristic photos of a datacenter and lines of code. Eventuelly flewent integrated in the text. On the landing page the company should introduced with a small text (max 250 words) followed by a section with a short text to one of our products nearby a graphic visualising the architecture of the product. The menue should be on top and fixed during scrolling and consist of the menue items home, solutions, who are we and a contact button. There should be a footer for linking social media, rights and Impressum. Only as an idea not a must. The very first view on the landing page could also be the menue bar and below of it a transparent unsharp photo (e.g. datacenter, lines of code, both ;) with the company name in the center.

###############################################################

Hi Designers,

Despite your very good approaches for describing QR.KA Horizon, here a short introduction (german text) from ourself:

------
QR.KA Horizon – Ihr Partner für ganzheitliche Softwarelösungen

Die QR.KA Horizon ist ein dynamisches Unternehmen, das sich nicht nur auf die Konzeption, das Design und die Entwicklung maßgeschneiderter Software spezialisiert hat, sondern auch deren reibungslosen Betrieb sicherstellt. Mit einem Team aus erfahrenen Softwarearchitekten und IT-Professionals verbinden wir modernste Softwareentwicklung mit tiefgehendem IT-Know-how – für Lösungen, die nachhaltig, leistungsstark und zukunftssicher sind.

Software Engineering trifft IT – Perfektion in Kombination
Software Engineering und IT sind zwei unterschiedliche Disziplinen – und doch untrennbar miteinander verbunden. Wir bei QR.KA Horizon vereinen beide Welten und sorgen dafür, dass unsere Softwarelösungen nicht nur innovativ und leistungsfähig sind, sondern sich auch perfekt in bestehende IT-Landschaften integrieren.

Expertise mit Fokus auf Healthcare & komplexe IT-Umgebungen
Unsere Experten bringen jahrzehntelange Erfahrung aus dem Healthcare-Sektor mit und unterstützen IT-Abteilungen großer Kliniken in der Entwicklung und Optimierung von Softwarelösungen. Von Anwendungssoftware bis hin zu Steuerungssystemen – unsere Softwareingenieure wissen genau, worauf es ankommt.

Ganzheitlicher Ansatz – über die Software hinaus
Wir entwickeln nicht nur Software, sondern übernehmen auch die Verantwortung für deren stabile und effiziente Betriebsumgebung. Egal, ob on-premises, in der Cloud oder als SaaS-Lösung – wir kümmern uns um den kompletten Lifecycle Ihrer Anwendung.

Ihre Vision – unsere Mission.
Ob Neuentwicklung einer SaaS-Anwendung oder die Migration bestehender Lösungen in eine moderne SaaS-Umgebung – mit QR.KA Horizon haben Sie einen starken Partner an Ihrer Seite.

Lassen Sie uns gemeinsam die Zukunft Ihrer Software gestalten!
--------------

Our first solution called "Clear Record Transfer Gateway" (CLURA)
-------------------
Teilen Sie Ihre Daten sicher – ohne Kompromisse!

Sie nutzen eine relationale Datenbank (Brightcask, Tabulon Hub, Vellumdb etc.) und möchten ausgewählte Daten mit Dritten teilen – sei es für ein Data Warehouse, Business Controller, Lieferanten oder Kunden? Doch dabei sollen Datensicherheit, Integrität und Verfügbarkeit Ihrer primären Lösung in keiner Weise gefährdet werden?

Mit unserer Lösung erhalten Sie genau das: Maximalen Schutz für Ihre Anwendung bei gleichzeitigem Nutzen durch autorisierte Dritte – ganz ohne teure Lizenzkosten für eine Schattendatenbank.

Lassen Sie uns gemeinsam herausfinden, wie Sie Ihre Daten sicher und effizient nutzen können. Kontaktieren Sie uns – wir zeigen Ihnen, was möglich ist!
---------------------

Our second solution MIVO:
---------------------
MIVO – Program for a Tone Matching Instrument ist die smarte Lösung für Unternehmen, die bei Farbgenauigkeit keine Kompromisse machen. Die Software erkennt Farbabweichungen zwischen Mustern vollautomatisch, beschreibt sie verständlich und sorgt so für gleichbleibend hohe Produktqualität – schnell, visuell und präzise. Perfekt für alle, die Farbe zur Vertrauenssache machen.
-------------------------

Thanks,
Gerold

Target Market(s)

IT Professionals from any sector

Industry/Entity Type

Healthcare and other

Coding

Coded - Design and coding required

Number of Pages Required

1 page

Font styles to use
Sans Serif

Colors
0054AA
0677BA
7BADD7
CADEEF
E8F1F8
0094D4
00A9DD
6FCCEA
C7EBF8
E9F6FB
00AB8E
00BBA5
67D7C9
C6EFE9
E9F9F6

Requirements
Must have
• Please see description
Nice to have
• On the landing page the company should introduced with a small text (max 250 words) followed by a section with a short text to one of our products nearby a graphic visualising the architecture of the product. The menue should be on top and fixed during scrolling and consist of the menue items home, solutions, who are we and a contact button. There should be a footer for linking social media, rights and Impressum. Only as an idea not a must. The very first view on the landing page could also be the menue bar and below of it a transparent unsharp photo (e.g. datacenter, lines of code, both ;) with the company name in the center.
Should not have
• Please see description

```html
<!DOCTYPE html>
<html lang="en">
<head>
<meta charset="utf-8">
<title>QR.KA Horizon</title>
<link href="https://fonts.googleapis.com/css2?family=Montserrat:wght@500;600;700;800&family=Mulish:wght@300;400;500;600&display=swap" rel="stylesheet">
<style>
  :root{
    --navy:#0f3166;
    --blue:#0054AA;
    --footer-blue:#1a4d9b;
    --rule-blue:#1a4d9b;
    --green:#1fa383;
    --ice:#e0f0fa;
    --white:#ffffff;
    --ink:#111111;
    --body-ink:#222222;
  }
  *{box-sizing:border-box;margin:0;padding:0}
  html,body{width:726px;height:1200px;overflow:hidden}
  body{font-family:"Mulish",sans-serif;color:var(--body-ink);background:var(--white);position:relative}
  .btn{display:inline-flex;align-items:center;justify-content:center;background:var(--green);color:var(--white);
    font-family:"Montserrat",sans-serif;font-weight:700;border-radius:999px;text-decoration:none;letter-spacing:.2px}

  /* hero */
  .hero{position:absolute;left:0;top:0;width:726px;height:415px;overflow:hidden}
  .hero-backdrop{position:absolute;inset:0;
    background:radial-gradient(ellipse at 50% 55%,#1d4f93 0%,#143f7d 40%,#0e2d62 100%)}
  .main-nav{position:absolute;top:21px;left:0;width:726px;display:flex;justify-content:center}
  .main-nav a{font-family:"Montserrat",sans-serif;font-weight:600;font-size:11.5px;color:var(--white);text-decoration:none;
    padding:5px 9px;border-radius:999px;margin:0 9px}
  .main-nav a.active{background:var(--green)}
  .hero-brand{position:absolute;top:150px;left:0;width:726px;text-align:center;color:var(--white);
    font-family:"Montserrat",sans-serif;font-weight:700;font-size:50px;line-height:1;letter-spacing:.5px}
  .hero-intro{position:absolute;top:252px;left:143px;width:440px;text-align:center;color:#eef4fb;font-size:10.6px;line-height:14.5px;font-weight:400}
  .hero .btn{position:absolute;top:349px;left:318px;width:91px;height:26px;font-size:8.5px}

  /* product */
  .product{position:absolute;top:415px;left:0;width:726px;height:268px}
  .section-title{font-family:"Montserrat",sans-serif;font-weight:800;font-size:20px;color:var(--ink);letter-spacing:.3px}
  .rule{height:1.5px;width:50px;background:var(--rule-blue)}
  .product .section-title{position:absolute;top:30px;left:91px}
  .product .rule{position:absolute;top:65px;left:91px}
  .product-text{position:absolute;top:88px;left:89px;width:226px;font-size:10.6px;line-height:16.4px;color:var(--body-ink)}
  .product .btn{position:absolute;top:208px;left:90px;width:75px;height:22px;font-size:7.5px}
  .product-visual{position:absolute;top:30px;left:343px;width:292px;height:207px;border-radius:8px;
    background:radial-gradient(ellipse at 45% 50%,#1c4a6a 0%,#14283f 55%,#0f1b2a 100%)}

  /* solutions */
  .solutions{position:absolute;top:683px;left:0;width:726px;height:316px;background:var(--ice)}
  .solutions .section-title{position:absolute;top:24px;left:0;width:726px;text-align:center}
  .solutions .rule{position:absolute;top:62px;left:337px}
  .cards{position:absolute;top:83px;left:89px;display:flex;gap:9.5px}
  .card{position:relative;width:130px;height:207px;background:var(--white);border-radius:7px}
  .card-icon{position:absolute;top:15px;left:19px;width:44px;height:44px;border-radius:50%;background:var(--footer-blue);display:flex;align-items:center;justify-content:center}
  .card h3{position:absolute;top:69px;left:18px;width:108px;font-family:"Montserrat",sans-serif;font-weight:700;font-size:10px;line-height:13.6px;color:var(--ink)}
  .card p{position:absolute;left:18px;width:98px;font-size:6.8px;line-height:9px;color:#333}
  .card .btn{position:absolute;top:177px;left:18px;width:52px;height:15px;font-size:5.3px}

  /* footer */
  .site-footer{position:absolute;top:999px;left:0;width:726px;height:201px;background:var(--footer-blue)}
  .cta{position:absolute;top:33px;left:91px;width:546px;height:55px;border-radius:28px;background:var(--ice)}
  .cta h4{position:absolute;top:14px;left:33px;font-family:"Montserrat",sans-serif;font-weight:800;font-size:11px;color:var(--footer-blue);letter-spacing:.2px}
  .cta p{position:absolute;top:30px;left:33px;font-size:9.4px;color:#222}
  .cta .btn{position:absolute;top:11px;left:418px;width:113px;height:32px;font-size:10.5px}
  .footer-brand{position:absolute;top:130px;left:92px;color:var(--white);font-family:"Montserrat",sans-serif;font-weight:700;font-size:24px;line-height:1}
  .follow{position:absolute;top:111px;left:500px;display:flex;align-items:center;gap:2px}
  .follow span{font-family:"Montserrat",sans-serif;font-weight:500;font-size:7.5px;color:var(--white);margin-right:10px;letter-spacing:.3px}
  .follow i{display:block;width:16px;height:16px;border-radius:50%;background:var(--white)}
  .footer-nav{position:absolute;top:1141px;left:0;right:89px;display:flex;justify-content:flex-end;gap:21px}
  .footer-nav a,.legal a,.legal span{font-family:"Montserrat",sans-serif;color:var(--white);text-decoration:none}
  .footer-nav a{font-size:8.5px;font-weight:500}
  .legal{position:absolute;top:1165px;right:89px;display:flex;gap:8px}
  .legal a,.legal span{font-size:7.3px;font-weight:500}
</style>
</head>
<body>

<section class="hero">
  <div class="hero-backdrop" role="img" aria-label="Blurred data center corridor overlaid with glowing binary code in deep blue"></div>
  <nav class="main-nav">
    <a href="#" class="active">HOME</a>
    <a href="#">SOLUTIONS</a>
    <a href="#">WHO ARE WE</a>
    <a href="#">CONTACT</a>
  </nav>
  <div class="hero-brand">QR.KA Horizon</div>
  <p class="hero-intro">At QR.KA Horizon, we bridge the gap between software engineering and IT infrastructure. While these disciplines operate differently, their synergy is what drives true innovation. We design powerful, scalable software solutions that integrate seamlessly into your IT ecosystem—ensuring efficiency, security, and future readiness. Our vision goes beyond technology; it’s about transforming possibilities into reality.</p>
  <a href="#" class="btn">READ MORE</a>
</section>

<section class="product">
  <h2 class="section-title">OUR PRODUCT</h2>
  <div class="rule"></div>
  <p class="product-text">Our Cloud Orchestration Platform automates deployment across hybrid environments, reducing complexity while maximizing scalability. Built with microservices and Podweave-native architecture, it adapts to your IT landscape effortlessly.</p>
  <a href="#" class="btn">READ MORE</a>
  <div class="product-visual" role="img" aria-label="Architecture visual of connected nodes and blocks glowing in cyan and magenta on a dark background"></div>
</section>

<section class="solutions">
  <h2 class="section-title">SOLUTIONS</h2>
  <div class="rule"></div>
  <div class="cards">
    <article class="card">
      <div class="card-icon">
        <svg width="28" height="28" viewBox="0 0 28 28" fill="none" stroke="#fff" stroke-width="1.5" stroke-linecap="round">
          <path d="M8 16h12a4 4 0 0 0 0-8 6 6 0 0 0-11.5-1A4.5 4.5 0 0 0 8 16z"/>
          <path d="M10 16v5M14 16v7M18 16v5"/><circle cx="10" cy="22" r="1.3"/><circle cx="14" cy="24" r="1.3"/><circle cx="18" cy="22" r="1.3"/>
        </svg>
      </div>
      <h3>Cloud Orchestration Platform</h3>
      <p style="top:118px">Automate deployments, scaling, and monitoring across Nimbra, Cobaltis, and on-premises environments with our Podweave-native orchestration engine.</p>
      <a href="#" class="btn">READ MORE</a>
    </article>
    <article class="card">
      <div class="card-icon">
        <svg width="30" height="30" viewBox="0 0 30 30" fill="none" stroke="#fff" stroke-width="1.5" stroke-linecap="round">
          <circle cx="15" cy="15" r="10"/><circle cx="11" cy="15" r="3"/><circle cx="19.5" cy="15" r="3"/>
          <path d="M11 10.5v1.5M11 18v1.5M6.5 15H8M19.5 10.5v1.5M19.5 18v1.5M24 15h-1.5"/>
        </svg>
      </div>
      <h3>DevSecOps Pipeline</h3>
      <p style="top:105px">Integrate security into every phase of your CI/CD pipeline—from static code analysis to runtime protection. We harden your DevOps workflow without slowing down releases.</p>
      <a href="#" class="btn">READ MORE</a>
    </article>
    <article class="card">
      <div class="card-icon">
        <svg width="28" height="28" viewBox="0 0 28 28" fill="none" stroke="#fff" stroke-width="1.5" stroke-linecap="round">
          <rect x="5" y="10" width="18" height="12" rx="1.5"/><path d="M10 25h8M14 22v3M14 3v5M11.5 5.5 14 3l2.5 2.5"/>
          <circle cx="14" cy="16" r="2.8"/>
        </svg>
      </div>
      <h3>Legacy System Modernization</h3>
      <p style="top:106px">Transform outdated monoliths into scalable microservices without business disruption. Our incremental modernization approach minimizes risk while maximizing agility.</p>
      <a href="#" class="btn">READ MORE</a>
    </article>
    <article class="card">
      <div class="card-icon">
        <svg width="30" height="30" viewBox="0 0 30 30" fill="none" stroke="#fff" stroke-width="1.4" stroke-linecap="round">
          <rect x="9" y="10" width="12" height="10" rx="1"/>
          <path d="M12 10V6M15 10V5M18 10V6M12 20v4M15 20v5M18 20v4M9 13H5M9 17H5M21 13h4M21 17h4"/>
          <text x="15" y="17.5" text-anchor="middle" font-family="Montserrat,sans-serif" font-size="6" fill="#fff" stroke="none">AI</text>
        </svg>
      </div>
      <h3>AI-Powered Observability Suite</h3>
      <p style="top:106px">Predict and resolve IT incidents before they impact users. Our machine learning engine correlates logs, metrics, and traces across your stack for actionable insights.</p>
      <a href="#" class="btn">READ MORE</a>
    </article>
  </div>
</section>

<footer class="site-footer">
  <div class="cta">
    <h4>LOREM IPSUM IS SIMPLY DUMMY TEXT</h4>
    <p>Contrary to popular belief, Lorem Ipsum is not simpl</p>
    <a href="#" class="btn">CONTACT US</a>
  </div>
  <div class="footer-brand">QR.KA Horizon</div>
  <div class="follow">
    <span>FOLLOW</span>
    <i></i><i></i><i></i><i></i><i></i>
  </div>
</footer>
<nav class="footer-nav">
  <a href="#">HOME</a><a href="#">SOLUTIONS</a><a href="#">WHO ARE WE</a><a href="#">CONTACT</a>
</nav>
<div class="legal">
  <a href="#">Impressum</a><span>|</span><a href="#">Terms and Conditions</a><span>|</span><span>Copyright © 2025 All Rights Reserved</span>
</div>

</body>
</html>
```